Talking Ledger Hour Podcast artwork

Podcast Artwork. Hosted by Marlow Teedquist. Also looking for a clear and distinct font that can be used as a logo for business cards and website. This podcast is a long format, conversation driven podcast about the stories behind cryptocurrencies and blockchain technology. We dive into what's exciting and what's to come and how industries, the internet, and the way we do business is being changed through this new technology. It will be conversation driven rather than tech heavy. Navy or Royal Blue and Hot Pink would be our first choices of colours.

Target Market(s)

Finance, Entertainment, Technology sectors.

Contact Information for Business Card

Marlow Teedquist
Podcast Host
@talkingledger
talkingledgerhour.example
talkingledger@mailnook.example

Logo Text

Talking Ledger Hour Podcast

Font styles to use
Sans Serif

Colors
0455a3
e667a6

Requirements
Must have
• Colours that match the website: talkingledgerhour.example
Nice to have
• A style that matches the website talking ledger hour.com

```html
<!DOCTYPE html>
<html lang="en">
<head>
<meta charset="utf-8">
<title>Talking Ledger Hour Podcast Artwork</title>
<link rel="stylesheet" href="https://fonts.googleapis.com/css2?family=Anton&family=Montserrat:ital,wght@0,800;1,800;1,900&display=swap">
<style>
  :root {
    --ledger-blue: #1279b8;
    --hot-coral: #f05f67;
    --slate-grey: #77777a;
    --paper: #ffffff;
  }
  html, body {
    margin: 0;
    padding: 0;
    width: 1200px;
    height: 1200px;
    overflow: hidden;
    background: var(--paper);
  }
  .artwork {
    position: relative;
    width: 1200px;
    height: 1200px;
    background: var(--paper);
  }
  .artwork-frame {
    position: absolute;
    left: 32px;
    top: 37px;
    width: 1078px;
    height: 1078px;
    border: 29px solid var(--hot-coral);
    box-sizing: content-box;
  }
  .artwork-svg {
    position: absolute;
    inset: 0;
  }
  .badge-circle { fill: var(--hot-coral); }
  .badge-name {
    fill: var(--paper);
    font-family: "Montserrat", sans-serif;
    font-weight: 800;
    font-size: 52px;
  }
  .title-top {
    fill: var(--ledger-blue);
    font-family: "Anton", sans-serif;
    font-size: 168px;
  }
  .title-of {
    fill: var(--slate-grey);
    font-family: "Anton", sans-serif;
    font-size: 66px;
  }
  .title-bottom {
    fill: var(--ledger-blue);
    font-family: "Montserrat", sans-serif;
    font-style: italic;
    font-weight: 900;
    font-size: 132px;
  }
  .host-name {
    fill: var(--hot-coral);
    font-family: "Montserrat", sans-serif;
    font-style: italic;
    font-weight: 800;
    font-size: 64px;
  }
</style>
</head>
<body>
  <main class="artwork">
    <div class="artwork-frame"></div>
    <svg class="artwork-svg" width="1200" height="1200" viewBox="0 0 1200 1200" xmlns="http://www.w3.org/2000/svg">
      <g class="show-badge">
        <circle class="badge-circle" cx="590" cy="376" r="205"/>
        <text class="badge-name" x="590" y="330" text-anchor="middle">Talking</text>
        <text class="badge-name" x="590" y="392" text-anchor="middle">Ledger</text>
        <text class="badge-name" x="590" y="454" text-anchor="middle">Hour</text>
      </g>
      <g class="show-title">
        <text class="title-top" x="182" y="796" textLength="682" lengthAdjust="spacingAndGlyphs">Talking</text>
        <text class="title-of" x="902" y="792" textLength="58" lengthAdjust="spacingAndGlyphs">of</text>
        <text class="title-bottom" x="372" y="948" textLength="690" lengthAdjust="spacingAndGlyphs">Ledger Hour</text>
      </g>
      <text class="host-name" x="272" y="1048" textLength="790" lengthAdjust="spacingAndGlyphs">MARLOW TEEDQUIST</text>
    </svg>
  </main>
</body>
</html>
```